Electric mountain bike tours nz

We are an Electric Mountain bike tour company in New Zealand. We will be offering bike rental and guided tours around the Nelson region in New Zealand. I want our website to represent both Mountain biking and New Zealand with the colours layout and features. We want tabs for the following:
-1 about us
-2 what we offer
-3 bookings/contact
Under the about us tab will be who we are as a a company. I want the ability to add videos to each of these tabs as we move foward with videos of the tracks we will be riding. I want the website to be editable so I can add and remove videos/photos myself. Also "our bikes" will be under this tab.
Under the what we offer tab will be
-1 bike rental and pricing
-2 guided tours and pricing
-3 recommended package deals.
I want to able to put the tracks under the guided tours tab and select beginner/ intermediate/advanced and have the tracks in each of the following to match the rider level. Also to be able to have a small video of the track would be great in this section.
Bookings and contact tab
(Further information for this tab to be updated soon)
Coded - Design and coding required
1 page
- Silver ferns, kiwi, mountains

```html
<!DOCTYPE html>
<html lang="en">
<head>
<meta charset="utf-8">
<title>Ridgevolt – Electric Mountain Bike Tours</title>
<link href="https://fonts.googleapis.com/css2?family=Poppins:wght@400;500;600;700&display=swap" rel="stylesheet">
<style>
:root{
  --orange:#d4761a;
  --black:#000;
  --white:#fff;
  --grey-bg:#e8e8e8;
  --field:#d4d4d4;
  --text:#333;
  --photo-light:#e6e6e6;
  --photo-mid:#cfcfcf;
  --kiwi-brown:#7a4f26;
}
*{margin:0;padding:0;box-sizing:border-box}
html,body{width:1200px;height:3495px;overflow:hidden}
body{font-family:'Poppins',sans-serif;color:var(--text);background:var(--white);position:relative}
.abs{position:absolute}
.center{text-align:center}
h2.section-title{position:absolute;left:0;width:1200px;text-align:center;color:var(--orange);font-size:36px;font-weight:600;line-height:1}

/* hero */
.hero{position:absolute;left:0;top:0;width:1200px;height:700px;background:linear-gradient(180deg,#4a4f52 0%,#3b3f3a 40%,#2f3328 70%,#23261f 100%)}
.hero-wave{position:absolute;left:0;top:560px;width:1200px;height:140px}
.nav{position:absolute;left:184px;top:51px;width:832px;height:73px;background:var(--white);font-size:15px;color:#222}
.nav a{position:absolute;top:26px;text-decoration:none;color:#222;line-height:21px}
.nav a.active{color:var(--orange)}
.brand{position:absolute;left:554px;top:16px;width:140px;height:140px;border-radius:50%;background:var(--white);border:5px solid #222;display:flex;align-items:center;justify-content:center;font-weight:700;font-size:19px;color:#222;letter-spacing:.5px}
.hero-kicker{top:225px;font-size:29px;line-height:40px;color:var(--white);font-weight:500}
.hero-title{top:266px;font-size:38px;line-height:46px;color:var(--white);font-weight:600}
.hero-text{top:318px;font-size:18px;color:var(--white);line-height:28px}
.btn-outline{position:absolute;left:527px;top:391px;width:146px;height:48px;border:2px solid var(--white);border-radius:24px;color:var(--white);font-size:14px;font-weight:600;display:flex;align-items:center;justify-content:center}
.dots{position:absolute;left:570px;top:510px;display:flex;gap:12px;align-items:center}
.dot{width:10px;height:10px;border-radius:50%;background:var(--white)}
.dot.current{width:18px;height:18px;border:2px solid var(--white);background:transparent;position:relative}
.dot.current::after{content:"";position:absolute;left:3px;top:3px;width:8px;height:8px;border-radius:50%;background:var(--white)}

/* about */
.bike-photo{position:absolute;left:93px;top:804px;width:500px;height:314px;background:linear-gradient(135deg,var(--photo-light) 0%,var(--photo-mid) 100%)}
.about-text{position:absolute;left:643px;top:822px;width:466px;font-size:15.5px;line-height:27.5px;color:#444}
.btn-solid{position:absolute;background:var(--orange);color:var(--white);border-radius:40px;font-weight:600;display:flex;align-items:center;justify-content:center}

/* offer */
.offer-band{position:absolute;left:0;top:1235px;width:1200px;height:342px;background:var(--black)}
.offer-text{top:1358px;font-size:15.5px;color:var(--white);line-height:28px}
.video{position:absolute;left:88px;top:1463px;width:1021px;height:490px;background:linear-gradient(180deg,#4b4c4a 0%,#3a3a31 45%,#514a3d 100%)}
.play{position:absolute;left:570px;top:1680px;width:58px;height:58px}

/* pricing */
.pricing{position:absolute;left:0;top:2013px;width:1200px;height:690px;background:var(--grey-bg)}
.pricing-text{top:2113px;font-size:15.5px;line-height:28px;color:#333}
.card{position:absolute;background:var(--white);box-shadow:0 2px 8px rgba(0,0,0,.12);text-align:center}
.card h3{font-size:24px;font-weight:600;color:var(--orange);margin-top:30px;line-height:34px}
.card .sub{font-size:15px;font-weight:600;color:#333;margin-top:6px}
.card .price{font-size:36px;font-weight:600;color:var(--orange);margin-top:4px;line-height:48px}
.card hr{border:none;border-top:1px solid #999;width:190px;margin:12px auto 10px}
.card ul{list-style:none;display:inline-block;text-align:left}
.card li{font-size:15px;line-height:29px;display:flex;align-items:center;gap:8px}
.card li svg{width:20px;height:20px}
.card .order{display:inline-flex;align-items:center;justify-content:center;background:var(--orange);color:var(--white);font-size:14px;font-weight:600;width:98px;height:34px;border-radius:17px}
.card.featured{background:var(--orange);box-shadow:none}
.card.featured h3,.card.featured .sub,.card.featured .price,.card.featured li{color:var(--white)}
.card.featured li{font-size:16.5px;line-height:33px}
.card.featured hr{border-top-color:#f0c9a0;width:220px}
.card.featured .order{background:#eee;color:#555;width:106px}

/* quote */
.quote{position:absolute;left:0;top:2703px;width:1200px;height:466px;background:linear-gradient(180deg,#f4f4f4 0%,#ececec 60%,#dcdcdc 100%)}
.quote-text{top:2795px;font-size:15.5px;color:#333}
.field{position:absolute;background:var(--field);font-size:13px;color:#777;padding:0 20px;display:flex;align-items:center}
.field.area{align-items:flex-start;padding-top:18px}
.kiwi{position:absolute;left:86px;top:3044px;width:112px;height:116px;background:var(--kiwi-brown)}

/* footer */
.footer{position:absolute;left:0;top:3169px;width:1200px;height:326px;background:var(--black);color:var(--white)}
.footer-brand{position:absolute;left:121px;top:45px;width:136px;height:136px;border-radius:50%;border:5px solid var(--white);display:flex;align-items:center;justify-content:center;font-weight:700;font-size:18px}
.socials{position:absolute;left:138px;top:211px;display:flex;gap:10px}
.socials span{width:13px;height:13px;border-radius:50%;background:var(--white)}
.footer h4{position:absolute;top:40px;font-size:17px;font-weight:600}
.links{position:absolute;left:363px;top:83px;list-style:none;font-size:15px;line-height:31px}
.contact-item{position:absolute;left:564px;display:flex;gap:12px;font-size:13px;line-height:20px}
.contact-item svg{width:16px;height:16px;flex:none;margin-top:2px}
.news-text{position:absolute;left:853px;top:80px;width:240px;font-size:13px;line-height:25px}
.news-form{position:absolute;left:853px;top:177px;width:240px;height:38px;background:var(--white);display:flex}
.news-form span{flex:1;font-size:11px;color:#666;padding-left:10px;display:flex;align-items:center}
.news-form b{width:40px;background:var(--orange);display:flex;align-items:center;justify-content:center}
.footer-rule{position:absolute;left:0;top:268px;width:1200px;border-top:1px solid #222}
.copyright{position:absolute;left:0;top:287px;width:1200px;text-align:center;font-size:12px}
</style>
</head>
<body>

<!-- Hero -->
<section class="hero" role="img" aria-label="Photo of two riders on electric mountain bikes in front of snowy mountains"></section>
<svg class="hero-wave" viewBox="0 0 1200 140" preserveAspectRatio="none" aria-hidden="true">
  <path d="M0 130 C200 100 380 90 560 95 C760 100 820 60 960 45 C1080 35 1150 40 1200 50 L1200 140 L0 140 Z" fill="#fff"/>
</svg>
<nav class="nav">
  <a class="active" style="left:32px">Home</a>
  <a style="left:124px">About us</a>
  <a style="left:242px">What we offer</a>
  <a style="left:536px">Bookings</a>
  <a style="left:657px">Contact us</a>
</nav>
<div class="brand">RIDGEVOLT</div>

<p class="abs center hero-kicker" style="left:0;width:1200px">Welcome To</p>
<h1 class="abs center hero-title" style="left:0;width:1200px">Electric Mountain Bike</h1>
<p class="abs center hero-text" style="left:0;width:1200px">Sed ut perspiciatis unde omnis iste natus error sit voluptatem<br>accusantium doloremque laudantium</p>
<div class="btn-outline">READ MORE</div>
<div class="dots"><span class="dot current"></span><span class="dot"></span><span class="dot"></span></div>

<!-- About -->
<h2 class="section-title" style="top:732px">About Us</h2>
<div class="bike-photo" role="img" aria-label="Photo of two electric mountain bikes"></div>
<p class="about-text">Sed ut perspiciatis unde omnis iste natus error sit voluptatem accusantium doloremque laudantium, totam rem aperiam, eaque ipsa quae ab illo inventore veritatis et quasi architecto beatae vitae dicta sunt explicabo. Nemo enim ipsam voluptatem quia voluptas sit aspernatur aut odit aut fugit, sed quia consequuntur magni dolores eos qui ratione voluptatem sequi nesciunt.</p>
<div class="btn-solid" style="left:643px;top:1049px;width:172px;height:65px;font-size:16px">READ MORE</div>

<!-- What we offer -->
<section class="offer-band"></section>
<h2 class="section-title" style="top:1294px">What we offer</h2>
<p class="abs center offer-text" style="left:0;width:1200px">Sed ut perspiciatis unde omnis iste natus error sit voluptatem accusantium doloremque<br>laudantium, totam rem aperiam, eaque ipsa quae ab illo inventore</p>
<div class="video" role="img" aria-label="Video still of a rider on a mountain trail"></div>
<svg class="play" viewBox="0 0 58 58" aria-hidden="true">
  <circle cx="29" cy="29" r="26" fill="none" stroke="#fff" stroke-width="4"/>
  <path d="M23 18 L40 29 L23 40 Z" fill="#fff"/>
</svg>

<!-- Pricing -->
<section class="pricing"></section>
<h2 class="section-title" style="top:2063px">Pricing</h2>
<p class="abs center pricing-text" style="left:0;width:1200px">At vero eos et accusamus et iusto odio dignissimos ducimus qui blanditiis praesentium<br>voluptatum deleniti atque corrupti quos dolores et</p>

<div class="card" style="left:121px;top:2218px;width:303px;height:382px">
  <h3>Basic</h3>
  <p class="sub">At vero eos et accusamus</p>
  <p class="price">$175</p>
  <hr>
  <ul>
    <li><svg viewBox="0 0 20 20"><path d="M2 11 L8 16 L18 3" stroke="#d4761a" stroke-width="3.5" fill="none"/></svg>At vero eos et</li>
    <li><svg viewBox="0 0 20 20"><path d="M2 11 L8 16 L18 3" stroke="#d4761a" stroke-width="3.5" fill="none"/></svg>At vero eos et</li>
    <li><svg viewBox="0 0 20 20"><path d="M2 11 L8 16 L18 3" stroke="#d4761a" stroke-width="3.5" fill="none"/></svg>At vero eos et</li>
    <li><svg viewBox="0 0 20 20"><path d="M2 11 L8 16 L18 3" stroke="#d4761a" stroke-width="3.5" fill="none"/></svg>At vero eos et</li>
  </ul>
  <hr>
  <span class="order">Order</span>
</div>

<div class="card featured" style="left:445px;top:2195px;width:338px;height:429px">
  <h3 style="font-size:27px;margin-top:30px">Standard</h3>
  <p class="sub">At vero eos et accusamus</p>
  <p class="price" style="font-size:39px">$575</p>
  <hr>
  <ul>
    <li><svg viewBox="0 0 20 20"><path d="M2 11 L8 16 L18 3" stroke="#fff" stroke-width="3.5" fill="none"/></svg>At vero eos et</li>
    <li><svg viewBox="0 0 20 20"><path d="M2 11 L8 16 L18 3" stroke="#fff" stroke-width="3.5" fill="none"/></svg>At vero eos et</li>
    <li><svg viewBox="0 0 20 20"><path d="M2 11 L8 16 L18 3" stroke="#fff" stroke-width="3.5" fill="none"/></svg>At vero eos et</li>
    <li><svg viewBox="0 0 20 20"><path d="M2 11 L8 16 L18 3" stroke="#fff" stroke-width="3.5" fill="none"/></svg>At vero eos et</li>
  </ul>
  <hr>
  <span class="order">Order</span>
</div>

<div class="card" style="left:804px;top:2218px;width:305px;height:382px">
  <h3>Premium</h3>
  <p class="sub">At vero eos et accusamus</p>
  <p class="price">$875</p>
  <hr>
  <ul>
    <li><svg viewBox="0 0 20 20"><path d="M2 11 L8 16 L18 3" stroke="#d4761a" stroke-width="3.5" fill="none"/></svg>At vero eos et</li>
    <li><svg viewBox="0 0 20 20"><path d="M2 11 L8 16 L18 3" stroke="#d4761a" stroke-width="3.5" fill="none"/></svg>At vero eos et</li>
    <li><svg viewBox="0 0 20 20"><path d="M2 11 L8 16 L18 3" stroke="#d4761a" stroke-width="3.5" fill="none"/></svg>At vero eos et</li>
    <li><svg viewBox="0 0 20 20"><path d="M2 11 L8 16 L18 3" stroke="#d4761a" stroke-width="3.5" fill="none"/></svg>At vero eos et</li>
  </ul>
  <hr>
  <span class="order">Order</span>
</div>

<!-- Request a quote -->
<section class="quote" role="img" aria-label="Faded photo of a road with motion blur"></section>
<h2 class="section-title" style="top:2745px">Request a Quote</h2>
<p class="abs center quote-text" style="left:0;width:1200px">At vero eos et accusamus et iusto odio dignissimos ducimus</p>
<div class="field" style="left:98px;top:2847px;width:310px;height:52px">Name</div>
<div class="field" style="left:431px;top:2847px;width:310px;height:52px">Email</div>
<div class="field" style="left:764px;top:2847px;width:310px;height:52px">Phone Number</div>
<div class="field area" style="left:98px;top:2922px;width:976px;height:105px">Message..</div>
<div class="btn-solid" style="left:513px;top:3052px;width:160px;height:56px;font-size:15px">SUBMIT</div>
<div class="kiwi" role="img" aria-label="Illustration of a kiwi bird"></div>

<!-- Footer -->
<footer class="footer">
  <div class="footer-brand">RIDGEVOLT</div>
  <div class="socials" aria-label="Social links"><span></span><span></span><span></span><span></span></div>

  <h4 style="left:363px">Links</h4>
  <ul class="links">
    <li>Home</li><li>About us</li><li>What we offer</li><li>Bookings</li><li>Contact us</li>
  </ul>

  <h4 style="left:564px">Contact Us</h4>
  <div class="contact-item" style="top:85px">
    <svg viewBox="0 0 16 16"><path d="M8 1 C4.5 1 3 3.5 3 6 C3 9.5 8 15 8 15 C8 15 13 9.5 13 6 C13 3.5 11.5 1 8 1 Z" fill="#fff"/><circle cx="8" cy="6" r="2" fill="#000"/></svg>
    <span># 42, Kowhai Lane,<br>Riverside, NL 7010</span>
  </div>
  <div class="contact-item" style="top:147px">
    <svg viewBox="0 0 16 16"><path d="M3 1 L6 1 L7 5 L5 6.5 C6 9 7 10 9.5 11 L11 9 L15 10 L15 13 C15 14 14 15 13 15 C6 14.5 1.5 10 1 3 C1 2 2 1 3 1 Z" fill="#fff"/></svg>
    <span>+64 3 555 0147</span>
  </div>
  <div class="contact-item" style="top:193px">
    <svg viewBox="0 0 16 16"><rect x="1" y="3" width="14" height="10" fill="#fff"/><path d="M1 3 L8 9 L15 3" stroke="#000" stroke-width="1.2" fill="none"/></svg>
    <span>hello@ridgevolt-tours.nz</span>
  </div>

  <h4 style="left:853px">Newsletter</h4>
  <p class="news-text">But I must explain to you how all this mistaken idea of denouncing pleasure and praising.</p>
  <div class="news-form"><span>Enter your email address</span><b><svg width="16" height="12" viewBox="0 0 16 12"><path d="M1 6 H14 M9 1 L14 6 L9 11" stroke="#fff" stroke-width="2" fill="none"/></svg></b></div>

  <div class="footer-rule"></div>
  <p class="copyright">© 2018 Copyrights | All Rights Reserved</p>
</footer>

</body>
</html>
```